UI Improvement for FlorKeep app

We are looking for a talented UI/UX designer to REFINE and enhance the visual design of our mobile application, FlorKeep. The app is fully functional, but we need a designer to improve its aesthetics by specifying design elements such as fonts, colors, spacing, and component styles.
Your task will be to analyze the CURRENT UI and provide detailed design specifications that will make the app more visually appealing, modern, and user-friendly.
TODO:
Review the existing FlorKeep app design (see attachments) and identify areas for visual improvement.
Provide a detailed UI style guide, including:
Typography (font choices, sizes, and weights)
Color palette (primary, secondary, and accent colors)
Component styling (buttons, forms, icons, and interactive elements)
Spacing and layout guidelines (margins, paddings, and alignment)
Ensure the design remains clean, modern, and professional while maintaining usability and accessibility.
Provide design mockups or visual examples (if possible) to illustrate the proposed changes.
Deliverables:
A UI Style Guide (PDF or Figma file) with specifications on fonts, colors, spacing, and UI components.
Optionally, before/after mockups or examples demonstrating the improvements.
Ideal Designer:
Strong experience in mobile UI/UX design.
Understanding of modern design trends and best practices.
Ability to communicate design choices clearly for easy developer implementation.
I have attached 7 images showcasing the main UI screens used in the FlorKeep app. These screens need visual enhancements to improve their overall look and user experience.
The images represent the current design in three key modes:
LIST Mode – Displays data in a structured list format.
READ Mode – Shows detailed information when a user selects an item.
ADD/EDIT Mode – Allows users to input or modify information.
Additionally, there is a ‘MORE’ page, which serves as a menu listing other features of the application.
Task Objective:
Please refine and improve these UIs to create a more modern, visually appealing, and user-friendly experience. Focus on typography, colors, spacing, and component styling to ensure a cohesive and polished design.
Look and feel
Each slider illustrates characteristics of the customer's brand and the style your logo design should communicate.

```html
<!DOCTYPE html>
<html lang="en">
<head>
<meta charset="utf-8">
<title>FlorKeep – App Screens</title>
<link href="https://fonts.googleapis.com/css2?family=DM+Sans:wght@400;500;700&display=swap" rel="stylesheet">
<style>
:root{
  --bg-a:#eaf3fb; --bg-b:#e5f4f2;
  --screen:#f5f9fd; --card:#ffffff;
  --blue:#2588d3; --blue-dark:#1c7cc7; --blue-soft:#4c9fdd;
  --teal:#1fb69a; --ink:#1c2530; --muted:#5a6570; --line:#e3e8ee; --field:#dfe4ea;
}
*{box-sizing:border-box;margin:0;padding:0}
html,body{width:1200px;height:733px;overflow:hidden}
body{font-family:"DM Sans",sans-serif;background:linear-gradient(135deg,var(--bg-a),var(--bg-b));position:relative;color:var(--ink)}
.phone{position:absolute;top:69px;width:305px;height:593px;background:var(--screen);border-radius:30px;box-shadow:0 10px 30px rgba(40,90,140,.12);overflow:hidden}
.abs{position:absolute}
.status{position:absolute;top:14px;left:13px;right:14px;height:16px;display:flex;justify-content:space-between;align-items:center;font-size:11px;font-weight:500}
.status .sys{display:flex;gap:9px;align-items:center}
.header{position:absolute;top:50px;left:14px;width:277px;height:39px;border-radius:20px;background:linear-gradient(90deg,var(--blue-dark),var(--blue));color:#fff;display:flex;align-items:center;justify-content:center;font-weight:700;font-size:15px}
.hbtn{position:absolute;top:2px;width:35px;height:35px;border-radius:50%;background:var(--blue-soft);display:flex;align-items:center;justify-content:center}
.kebab{position:absolute;right:11px;top:12px}
.card{position:absolute;left:14px;width:277px;background:var(--card);border-radius:14px}
.field{position:absolute;height:35px;border:1px solid var(--field);border-radius:3px;background:#fff;font-size:9.5px;display:flex;align-items:center;padding-left:12px;justify-content:space-between;padding-right:10px;color:#2a323a}
.dots{position:absolute}
.nav{position:absolute;bottom:0;left:0;width:305px;height:48px;background:linear-gradient(90deg,var(--teal),var(--blue));display:flex;justify-content:space-around;align-items:center;color:#fff;font-size:9.5px;font-weight:500}
.nav .item{display:flex;flex-direction:column;align-items:center;gap:3px;opacity:.45}
.nav .item.on{opacity:1;font-weight:700}
.nav.full .item{opacity:.9}
.nav.full .item.on{opacity:1}
.letter{position:absolute;left:12px;font-size:10px}
.avatar{position:absolute;left:12px;width:27px;height:27px;border-radius:50%;color:#fff;font-weight:700;font-size:13px;display:flex;align-items:center;justify-content:center}
.pname{position:absolute;left:47px;font-size:11.5px;white-space:nowrap}
.pdate{position:absolute;left:47px;font-size:7.5px;color:var(--muted)}
.menu-item{position:absolute;left:27px;width:230px;height:41px;display:flex;align-items:center;gap:9px;font-size:11.5px;border-bottom:1px solid var(--line)}
.menu-item svg{width:13px;height:13px;fill:#1c2530}
</style>
</head>
<body>

<!-- Contact edit screen -->
<section class="phone" style="left:67px">
  <div class="status"><span>10: 37 AM</span><span class="sys">
    <svg width="12" height="9"><rect x="0" y="7" width="2" height="2" fill="#111"/><rect x="3" y="5" width="2" height="4" fill="#111"/><rect x="6" y="3" width="2" height="6" fill="#111"/><rect x="9" y="0" width="2" height="9" fill="#111"/></svg>
    <svg width="13" height="10" viewBox="0 0 13 10"><path d="M1 3.5a8 8 0 0 1 11 0M3 5.6a5 5 0 0 1 7 0M5 7.6a2.2 2.2 0 0 1 3 0" stroke="#111" stroke-width="1.4" fill="none"/><circle cx="6.5" cy="9" r="1" fill="#111"/></svg>
    <svg width="16" height="9"><rect x=".5" y=".5" width="13.5" height="8" rx="1.5" fill="none" stroke="#111"/><rect x="2" y="2" width="10.5" height="5" fill="#111"/><rect x="14.5" y="3" width="1.5" height="3" fill="#111"/></svg></span></div>
  <div class="header">Contact
    <span class="hbtn" style="left:2px"><svg width="12" height="12" viewBox="0 0 12 12"><path d="M11 6H2M6 1.5 1.5 6 6 10.5" stroke="#fff" stroke-width="2" fill="none"/></svg></span>
    <span class="hbtn" style="right:24px"><svg width="10" height="12" viewBox="0 0 10 12"><path d="M1 0h8v12L5 9 1 12z" fill="#fff"/></svg></span>
    <svg class="kebab" width="4" height="15"><circle cx="2" cy="2" r="1.7" fill="#fff"/><circle cx="2" cy="7.5" r="1.7" fill="#fff"/><circle cx="2" cy="13" r="1.7" fill="#fff"/></svg>
  </div>
  <div class="card" style="top:110px;height:192px"></div>
  <div class="field" style="top:123px;left:27px;width:241px">Business Name -e</div>
  <svg class="dots" style="top:133px;left:275px" width="4" height="15"><circle cx="2" cy="2" r="1.7" fill="var(--blue)"/><circle cx="2" cy="7.5" r="1.7" fill="var(--blue)"/><circle cx="2" cy="13" r="1.7" fill="var(--blue)"/></svg>
  <div class="field" style="top:167px;left:27px;width:252px">First Name -e</div>
  <div class="field" style="top:210px;left:27px;width:252px">Middle Name -e</div>
  <div class="field" style="top:253px;left:27px;width:252px">Last Name -e</div>

  <div class="card" style="top:319px;height:260px"></div>
  <div class="field" style="top:332px;left:27px;width:241px">AddressLabeTag -e<svg width="8" height="5"><path d="M1 1l3 3 3-3" stroke="#333" fill="none"/></svg></div>
  <svg class="dots" style="top:342px;left:275px" width="4" height="15"><circle cx="2" cy="2" r="1.7" fill="var(--blue)"/><circle cx="2" cy="7.5" r="1.7" fill="var(--blue)"/><circle cx="2" cy="13" r="1.7" fill="var(--blue)"/></svg>
  <div class="field" style="top:376px;left:27px;width:252px">AddressLine1 -e</div>
  <div class="field" style="top:419px;left:27px;width:252px">AddressLine2 -e</div>
  <div class="field" style="top:462px;left:27px;width:122px">AddressCity</div>
  <div class="field" style="top:462px;left:158px;width:122px">AddressState<svg width="8" height="5"><path d="M1 1l3 3 3-3" stroke="#333" fill="none"/></svg></div>
  <div class="field" style="top:506px;left:27px;width:252px">ZipCode</div>

  <nav class="nav full">
    <div class="item on"><svg width="11" height="12" viewBox="0 0 11 12"><circle cx="5.5" cy="3" r="3" fill="#fff"/><path d="M0 12a5.5 5 0 0 1 11 0z" fill="#fff"/></svg>Contact</div>
    <div class="item"><svg width="12" height="10" viewBox="0 0 12 10"><path d="M0 4h4v6H0zM0 4q0-4 4-4v2q-2 0-2 2M7 4h4v6H7zM7 4q0-4 4-4v2q-2 0-2 2" fill="#fff"/></svg>Quote</div>
    <div class="item"><svg width="13" height="11"><rect y="2" width="13" height="9" rx="1.5" fill="#fff"/><rect x="4" y="0" width="5" height="3" rx="1" fill="none" stroke="#fff"/></svg>WorkOrder</div>
    <div class="item"><svg width="10" height="12"><rect width="10" height="12" rx="1" fill="#fff"/><path d="M2 3h6M2 6h6M2 9h4" stroke="#2a8cc8"/></svg>Invoice</div>
    <div class="item"><svg width="14" height="4"><circle cx="2" cy="2" r="1.7" fill="#fff"/><circle cx="7" cy="2" r="1.7" fill="#fff"/><circle cx="12" cy="2" r="1.7" fill="#fff"/></svg>More</div>
  </nav>
</section>

<!-- Pilots list screen -->
<section class="phone" style="left:442px">
  <div class="status"><span>10: 37 AM</span><span class="sys">
    <svg width="12" height="9"><rect x="0" y="7" width="2" height="2" fill="#111"/><rect x="3" y="5" width="2" height="4" fill="#111"/><rect x="6" y="3" width="2" height="6" fill="#111"/><rect x="9" y="0" width="2" height="9" fill="#111"/></svg>
    <svg width="13" height="10" viewBox="0 0 13 10"><path d="M1 3.5a8 8 0 0 1 11 0M3 5.6a5 5 0 0 1 7 0M5 7.6a2.2 2.2 0 0 1 3 0" stroke="#111" stroke-width="1.4" fill="none"/><circle cx="6.5" cy="9" r="1" fill="#111"/></svg>
    <svg width="16" height="9"><rect x=".5" y=".5" width="13.5" height="8" rx="1.5" fill="none" stroke="#111"/><rect x="2" y="2" width="10.5" height="5" fill="#111"/><rect x="14.5" y="3" width="1.5" height="3" fill="#111"/></svg></span></div>
  <div class="header">Pilots
    <span class="hbtn" style="left:2px"><svg width="11" height="11"><path d="M5.5 0v11M0 5.5h11" stroke="#fff" stroke-width="2"/></svg></span>
    <svg class="kebab" width="4" height="15"><circle cx="2" cy="2" r="1.7" fill="#fff"/><circle cx="2" cy="7.5" r="1.7" fill="#fff"/><circle cx="2" cy="13" r="1.7" fill="#fff"/></svg>
  </div>
  <div class="card" style="top:110px;height:470px">
    <span class="letter" style="top:18px">A</span>
    <span class="avatar" style="top:37px;background:#29b6e0">A</span>
    <span class="pname" style="top:35px">Ashby, Colin, Brett, 5204718,</span>
    <span class="pdate" style="top:54px">30 Sept 24</span>

    <span class="letter" style="top:83px">B</span>
    <span class="avatar" style="top:102px;background:#55b855">B</span>
    <span class="pname" style="top:100px">Bellamy, Rowan, 6173092</span>
    <span class="pdate" style="top:118px">28 Feb 25</span>
    <span class="avatar" style="top:147px;background:#a8c43a">B</span>
    <span class="pname" style="top:145px">Brandel, Owen, 3940261,</span>
    <span class="pdate" style="top:163px">10 Oct 24</span>

    <span class="letter" style="top:194px">C</span>
    <span class="avatar" style="top:214px;background:#e23e8a">C</span>
    <span class="pname" style="top:212px">Corva, Eva, Selene, 7281604</span>
    <span class="pdate" style="top:231px">30 Mar 25</span>
    <span class="avatar" style="top:260px;background:#8e44ad">C</span>
    <span class="pname" style="top:266px">Cano Ferrer, Hugo, Marisel,</span>

    <span class="letter" style="top:313px">G</span>
    <span class="avatar" style="top:332px;background:#4b3fd8">G</span>
    <span class="pname" style="top:330px">Gorman, Cole, 8152937</span>
    <span class="pdate" style="top:348px">28 Feb 25</span>
    <span class="avatar" style="top:378px;background:#8a3fdc">G</span>
    <span class="pname" style="top:377px">Grant, Jonah, Alder, 4619380</span>
    <span class="pdate" style="top:394px">03 Jun 23</span>
  </div>
  <nav class="nav">
    <div class="item"><svg width="11" height="12" viewBox="0 0 11 12"><circle cx="5.5" cy="3" r="3" fill="#fff"/><path d="M0 12a5.5 5 0 0 1 11 0z" fill="#fff"/></svg>Contact</div>
    <div class="item on"><svg width="12" height="13" viewBox="0 0 12 13"><rect x="3" y="0" width="6" height="2" fill="#fff"/><circle cx="6" cy="4.5" r="2.5" fill="#fff"/><path d="M0 13a6 5.5 0 0 1 12 0z" fill="#fff"/></svg>Pilot</div>
    <div class="item"><svg width="12" height="12" viewBox="0 0 12 12"><path d="M11 1 7 5l1 6-1.5 1-2-5L2 9.5V11L1 12 0 10l2-2V7l1.5-1-1.7-3L3 2l3 2 4-4z" fill="#fff"/></svg>Plane</div>
    <div class="item"><svg width="10" height="12"><rect width="10" height="12" rx="1" fill="#fff"/><path d="M2 3h6M2 6h6M2 9h4" stroke="#2a8cc8"/></svg>Fit Request</div>
    <div class="item"><svg width="14" height="4"><circle cx="2" cy="2" r="1.7" fill="#fff"/><circle cx="7" cy="2" r="1.7" fill="#fff"/><circle cx="12" cy="2" r="1.7" fill="#fff"/></svg>More</div>
  </nav>
</section>

<!-- More menu screen -->
<section class="phone" style="left:818px">
  <div class="status"><span>10: 37 AM</span><span class="sys">
    <svg width="12" height="9"><rect x="0" y="7" width="2" height="2" fill="#111"/><rect x="3" y="5" width="2" height="4" fill="#111"/><rect x="6" y="3" width="2" height="6" fill="#111"/><rect x="9" y="0" width="2" height="9" fill="#111"/></svg>
    <svg width="13" height="10" viewBox="0 0 13 10"><path d="M1 3.5a8 8 0 0 1 11 0M3 5.6a5 5 0 0 1 7 0M5 7.6a2.2 2.2 0 0 1 3 0" stroke="#111" stroke-width="1.4" fill="none"/><circle cx="6.5" cy="9" r="1" fill="#111"/></svg>
    <svg width="16" height="9"><rect x=".5" y=".5" width="13.5" height="8" rx="1.5" fill="none" stroke="#111"/><rect x="2" y="2" width="10.5" height="5" fill="#111"/><rect x="14.5" y="3" width="1.5" height="3" fill="#111"/></svg></span></div>
  <div class="header">More
    <svg class="kebab" width="4" height="15"><circle cx="2" cy="2" r="1.7" fill="#fff"/><circle cx="2" cy="7.5" r="1.7" fill="#fff"/><circle cx="2" cy="13" r="1.7" fill="#fff"/></svg>
  </div>
  <div class="card" style="top:110px;height:470px"></div>
  <div class="menu-item" style="top:118px"><svg viewBox="0 0 12 12"><path d="M11 1 7 5l1 6-1.5 1-2-5L2 9.5V11L1 12 0 10l2-2V7l1.5-1-1.7-3L3 2l3 2 4-4z"/></svg>Flight</div>
  <div class="menu-item" style="top:162px"><svg viewBox="0 0 12 12"><path d="M0 5h5V3l3 3-3 3V7H0z"/><path d="M6 1h5v10H6" stroke="#1c2530" stroke-width="1.5" fill="none"/></svg>Login</div>
  <div class="menu-item" style="top:203px"><svg viewBox="0 0 12 12"><circle cx="6" cy="3" r="3"/><path d="M1 12a5 5 0 0 1 10 0z"/></svg>Account</div>
  <div class="menu-item" style="top:244px"><svg viewBox="0 0 12 12"><rect x=".7" y="1.7" width="10.6" height="9.6" fill="none" stroke="#1c2530" stroke-width="1.2"/><path d="M0 1h12v3H0zM3 0v2M9 0v2M3 6h2v2H3zM7 6h2v2H7z"/></svg>Calendar</div>
  <div class="menu-item" style="top:284px"><svg viewBox="0 0 12 12"><circle cx="3" cy="3.5" r="2"/><circle cx="9" cy="3.5" r="2"/><circle cx="6" cy="5" r="2.3"/><path d="M0 10a3 3 0 0 1 5-2M12 10a3 3 0 0 0-5-2M2 12a4 4 0 0 1 8 0z"/></svg>Users</div>
  <div class="menu-item" style="top:324px"><svg viewBox="0 0 12 12"><path d="M6 0 0 6h2v6h3V8h2v4h3V6h2z"/></svg>Dashboard</div>
  <div class="menu-item" style="top:365px"><svg viewBox="0 0 12 12"><path d="M0 1l3.5 1.3v10L0 11zM4.5 2.3 7.5 1v10l-3 1.3zM8.5 1 12 2.3v10L8.5 11z"/></svg>Tracking</div>
  <div class="menu-item" style="top:406px"><svg viewBox="0 0 12 12"><path d="M0 4h12v3H0zM1 7h10v5H1z"/><path d="M6 4V12" stroke="#fff"/><path d="M6 4C4 0 2 2 4 4M6 4c2-4 4-2 2 0" stroke="#1c2530" fill="none"/></svg>Outreach Event</div>
  <div class="menu-item" style="top:446px"><svg viewBox="0 0 12 12"><path d="M3 0h6v1.5H8v4l2 2H2l2-2v-4H3zM5.4 7.5h1.2V12H5.4z"/></svg>Maintenance Resource</div>
  <div class="menu-item" style="top:487px"><svg viewBox="0 0 12 12"><circle cx="4" cy="7" r="3.3" fill="none" stroke="#1c2530" stroke-width="2" stroke-dasharray="1.6 1"/><circle cx="9" cy="3" r="2.2" fill="none" stroke="#1c2530" stroke-width="1.6" stroke-dasharray="1.2 .8"/></svg>Setting</div>
  <nav class="nav">
    <div class="item"><svg width="11" height="12" viewBox="0 0 11 12"><circle cx="5.5" cy="3" r="3" fill="#fff"/><path d="M0 12a5.5 5 0 0 1 11 0z" fill="#fff"/></svg>Contact</div>
    <div class="item"><svg width="12" height="13" viewBox="0 0 12 13"><rect x="3" y="0" width="6" height="2" fill="#fff"/><circle cx="6" cy="4.5" r="2.5" fill="#fff"/><path d="M0 13a6 5.5 0 0 1 12 0z" fill="#fff"/></svg>Pilot</div>
    <div class="item"><svg width="12" height="12" viewBox="0 0 12 12"><path d="M11 1 7 5l1 6-1.5 1-2-5L2 9.5V11L1 12 0 10l2-2V7l1.5-1-1.7-3L3 2l3 2 4-4z" fill="#fff"/></svg>Plane</div>
    <div class="item"><svg width="10" height="12"><rect width="10" height="12" rx="1" fill="#fff"/><path d="M2 3h6M2 6h6M2 9h4" stroke="#2a8cc8"/></svg>Fit Request</div>
    <div class="item on"><svg width="14" height="4"><circle cx="2" cy="2" r="1.7" fill="#fff"/><circle cx="7" cy="2" r="1.7" fill="#fff"/><circle cx="12" cy="2" r="1.7" fill="#fff"/></svg>More</div>
  </nav>
</section>

</body>
</html>
```